verdant terraces simple classy business card design

my name is colin barrow and I run a gardening business aimed at high class verdant terraces. the business name is verdant terraces and our logo was designed on pixel harbour .My clientel are anything from residential homes to businesses. I take pride in my work and know that I offer a service like no other in my area.
The business card will be used to represent my business and I want it to be not only rememberable, but simplistic and modern. Eye catching too. Of course I would like it relatable to gardening and appealing to the correct clientel - those being garden enthusiasts, prestigious homes and businesses that are after top of the line gardening services like no other on the market.
I am not a typical lawn mowing business so I don't want a typical card design that represents that. The gardens I work with are generally million dollar properties with owners who are very garden proud looking for upkeep and guidance from me along with sometimes whole new garden designs. I want the business cards to show to my clients that I take pride, as they do, in their garden. And I want them to know from my card that I am a professional, qualified horticulturist offering them a top of the line service for life. I want them to refer my business on. I want them to look at my business card and see class and professionalism in a modern unique bold way.
The card should be simple with the possibility of the logo on the front being embossed/debossed and my details on the back the card should have a organic garden feel it's very important to me that it is absolutely perfect
I am also very open to ideas and suggestions so look forward to seeing the designs. the business logo has been supplied with this project and I want the card to be double sided

Contact info is
Colin Barrow - Managing Director / Horticulturist
Phone : 0481 526 704
Email: colinbarrow@verdantterraces.example.au

Target Market(s)

high class gardens residential and commercial

Industry/Entity Type

Gardener

Contact Information for Business Card

Contact info is
Phone : 0481 526 704

PLEASE MAKE CARD DOUBLE SIDED

Requirements
Must have
• organic simple classy modern feel
• must flow with the current logo that has been supplied with this project
• Double sided
• Must explain in a simple way that I deal with high end gardens and I'm a qualified horticulturist
Nice to have
• embossed debossed logo
Should not have
• shouldn't be to busy or cheap looking

```html
<!DOCTYPE html>
<html lang="en">
<head>
<meta charset="utf-8">
<title>Verdant Terraces – Business Card</title>
<link rel="stylesheet" href="https://fonts.googleapis.com/css2?family=Noto+Serif:wght@400&display=swap">
<style>
  :root {
    --backdrop: #e6e2dc;
    --card: #f3f1ec;
    --frame-dark: rgba(120, 112, 100, 0.28);
    --frame-light: rgba(255, 255, 255, 0.9);
    --brand-green: #4f9a3e;
    --ink: #4a4a48;
  }
  * { box-sizing: border-box; margin: 0; padding: 0; }
  html, body {
    width: 1011px;
    height: 1200px;
    overflow: hidden;
    background: var(--backdrop);
  }
  .canvas {
    width: 1011px;
    height: 1200px;
    display: flex;
    flex-direction: column;
    align-items: center;
    justify-content: center;
    gap: 70px;
  }
  .card {
    position: relative;
    width: 840px;
    height: 480px;
    background: var(--card);
    box-shadow: 0 10px 28px rgba(60, 50, 40, 0.18), 0 2px 4px rgba(60, 50, 40, 0.12);
    display: flex;
    align-items: center;
    justify-content: center;
    font-family: "Noto Serif", Georgia, serif;
  }
  .card__frame {
    position: absolute;
    inset: 44px;
    border-radius: 16px;
    border: 2px solid var(--frame-dark);
    box-shadow: inset 1px 1px 0 var(--frame-light), 1px 1px 0 var(--frame-light);
  }
  .brand {
    position: relative;
    display: flex;
    flex-direction: column;
    align-items: center;
    color: var(--brand-green);
    font-weight: 400;
    text-transform: uppercase;
    line-height: 1;
  }
  .brand__dot {
    width: 86px;
    height: 86px;
    border-radius: 50%;
    background: var(--brand-green);
    margin-bottom: 22px;
  }
  .brand__name {
    font-size: 52px;
    letter-spacing: 1px;
  }
  .brand__sub {
    font-size: 30px;
    letter-spacing: 22px;
    margin-top: 6px;
    margin-right: -22px;
  }
  .contact {
    position: relative;
    text-align: center;
    color: var(--ink);
    font-weight: 400;
  }
  .contact__name { font-size: 30px; line-height: 1.15; }
  .contact__role { font-size: 19px; line-height: 1.3; }
  .contact__tagline {
    font-size: 15px;
    letter-spacing: 2px;
    text-transform: uppercase;
    color: var(--brand-green);
    margin-top: 8px;
    margin-bottom: 22px;
  }
  .contact__line { font-size: 19px; line-height: 1.3; }
</style>
</head>
<body>
  <main class="canvas">
    <section class="card card--front" aria-label="Card front">
      <div class="card__frame"></div>
      <div class="brand">
        <span class="brand__dot"></span>
        <span class="brand__name">Verdant</span>
        <span class="brand__sub">Terraces</span>
      </div>
    </section>

    <section class="card card--back" aria-label="Card back">
      <div class="card__frame"></div>
      <div class="contact">
        <p class="contact__name">Colin Barrow</p>
        <p class="contact__role">Managing Director · Qualified Horticulturist</p>
        <p class="contact__tagline">High-End Residential &amp; Commercial Gardens</p>
        <p class="contact__line">0481 526 704</p>
        <p class="contact__line">colinbarrow@verdantterraces.example.au</p>
      </div>
    </section>
  </main>
</body>
</html>
```